Outdoor fair Banner, Raspberry product company

I need a 10 foot long by 2.5 foot tall (height) designed banner for our outdoor booth. Please see previous design on the attached material.

I want it to be very eye catching, maybe use colors and such to make it look very professional.

Please use the logo and if you feel it would be appropriate, use the product photo as well.

Please do something that is reminiscent of raspberries, our label, our products, or a rustic look.

Industry/Entity Type

It Company

Font styles to use
Serif
Script

Colors
ec1f27
ffffff
faa54b
fac994
f68e4e

Requirements
Must have
• logo, more than just white background, very eye catching.
Nice to have
• product photo

```html
<!DOCTYPE html>
<html lang="en">
<head>
<meta charset="utf-8">
<title>Nora's Pine Hollow – Fair Banner Options</title>
<link href="https://fonts.googleapis.com/css2?family=Alegreya:ital,wght@1,500&display=swap" rel="stylesheet">
<style>
  :root {
    --page: #ffffff;
    --ink-number: #333333;
    --banner-deep: #1a0606;
    --banner-mid: #5e1518;
    --banner-glow: #8e2a2c;
    --title-white: #ffffff;
    --accent-orange: #f6a04a;
    --band-orange: #f59334;
    --band-text: #7a2226;
    --photo-light: #efe6e2;
    --photo-berry: #8e1d27;
  }
  html, body {
    margin: 0;
    width: 1200px;
    height: 1200px;
    overflow: hidden;
    background: var(--page);
  }
  .canvas { position: relative; width: 1200px; height: 1200px; }
  .banner {
    position: absolute;
    left: 62px;
    width: 982px;
    height: 327px;
  }
  .banner--one { top: 51px; }
  .banner--two { top: 438px; }
  .banner--three { top: 818px; }
  .option-number {
    position: absolute;
    left: 1104px;
    font: 400 26px Arial, Helvetica, sans-serif;
    color: var(--ink-number);
  }
  .banner-title {
    font-family: "Alegreya", Georgia, serif;
    font-style: italic;
    font-weight: 500;
    fill: var(--title-white);
  }
  .tagline {
    font-family: "Alegreya", Georgia, serif;
    font-style: italic;
    font-weight: 500;
  }
  .tagline--orange { fill: var(--accent-orange); }
  .tagline--white { fill: var(--title-white); }
  .tagline--band { fill: var(--band-text); }
  .tag-band { fill: var(--band-orange); }
</style>
</head>
<body>
<div class="canvas">
  <svg width="0" height="0" style="position:absolute">
    <defs>
      <radialGradient id="bannerGround" cx="0.45" cy="0.5" r="0.7">
        <stop offset="0" stop-color="var(--banner-glow)"/>
        <stop offset="0.55" stop-color="var(--banner-mid)"/>
        <stop offset="1" stop-color="var(--banner-deep)"/>
      </radialGradient>
      <linearGradient id="photoTone" x1="0" y1="0" x2="0" y2="1">
        <stop offset="0" stop-color="var(--photo-berry)" stop-opacity="0"/>
        <stop offset="0.25" stop-color="var(--photo-berry)"/>
        <stop offset="0.8" stop-color="var(--photo-berry)"/>
        <stop offset="1" stop-color="var(--photo-light)"/>
      </linearGradient>
    </defs>
  </svg>

  <svg class="banner banner--one" viewBox="0 0 982 327">
    <rect width="982" height="327" fill="url(#bannerGround)"/>
    <rect x="578" y="181" width="404" height="146" fill="url(#photoTone)" role="img" aria-label="Product photo: row of raspberry jam jars and syrup bottles with fresh raspberries"/>
    <text class="banner-title" x="50" y="150" font-size="120" textLength="856" lengthAdjust="spacingAndGlyphs">Nora’s Pine Hollow</text>
    <text class="tagline tagline--orange" x="110" y="289" font-size="50" textLength="380" lengthAdjust="spacingAndGlyphs">Raspberry Products</text>
  </svg>
  <div class="option-number" style="top:220px">1</div>

  <svg class="banner banner--two" viewBox="0 0 982 327">
    <rect width="982" height="327" fill="url(#bannerGround)"/>
    <rect x="482" y="142" width="500" height="185" fill="url(#photoTone)" role="img" aria-label="Product photo: row of raspberry jam jars and syrup bottles with fresh raspberries"/>
    <text class="banner-title" x="98" y="162" font-size="120" textLength="312" lengthAdjust="spacingAndGlyphs">Nora’s</text>
    <text class="banner-title" x="34" y="266" font-size="104" textLength="420" lengthAdjust="spacingAndGlyphs">Pine Hollow</text>
    <text class="tagline tagline--white" x="578" y="106" font-size="42" textLength="296" lengthAdjust="spacingAndGlyphs">Raspberry Products</text>
  </svg>
  <div class="option-number" style="top:596px">2</div>

  <svg class="banner banner--three" viewBox="0 0 982 327">
    <rect width="982" height="327" fill="url(#bannerGround)"/>
    <rect x="572" y="170" width="410" height="157" fill="url(#photoTone)" role="img" aria-label="Product photo: row of raspberry jam jars and syrup bottles with fresh raspberries"/>
    <text class="banner-title" x="70" y="162" font-size="160" textLength="396" lengthAdjust="spacingAndGlyphs">Nora’s</text>
    <text class="banner-title" x="492" y="158" font-size="100" textLength="418" lengthAdjust="spacingAndGlyphs">Pine Hollow</text>
    <path class="tag-band" d="M0 214 H490 Q510 214 510 234 V289 H0 Z"/>
    <text class="tagline tagline--band" x="62" y="266" font-size="58" textLength="426" lengthAdjust="spacingAndGlyphs">Raspberry Products</text>
  </svg>
  <div class="option-number" style="top:968px">3</div>
</div>
</body>
</html>
```